Stationery Design Project for Marketing Consultancy

I have started a new consultancy business and require the following elements to be designed using existing logo:
• Business card
• Letterhead
• Envelope (DL, C4, C5)
• Microsoft word template for report writing
• A4 Presentation Folder
• Powerpoint template
COPY FOR FRONT AND BACK OF BUSINESS CARD
logo
'Measurable Marketing. Epic Results' slogan (but no need to use existing lockup with logo)
name, B Com. Strategy, Grad Cert Brand Mgmt, MIM (post nominal abbreviations in smaller font)
mobile: 04XX-XXX-XXX (I will give details to the winner to add)
website: www.tolvarin.com.au
email: info@tolvarin.com.au
COPY FOR LETTERHEAD
Logo
Company Name
Please, submit your designs that include business card, letterhead and envelope. Once selected the winner will be asked to complete the project by creating the rest of the artwork.
FINAL FILES
Print ready files to be supplied as well as Indesign files so that minor amends can be made if necessary in future.
• Layered vectors in EPS & PDF
• Screen quality JPEG & PNGs
ABOUT THE BUSINESS: TOLVARIN
I work with clients to understand their business challenges, developing and executing measurable marketing strategies tied to key business metrics. Services include:
Services include:
• Business planning and business development
• Marketing and brand strategy
• Insight-driven integrated campaigns
• Loyalty programs and retention marketing
• Marketing automation
• Direct marketing (traditional and digital)
• Content strategy and development
Hi everyone,
Target Market(s)
Corporate decision makers (heads of marketing, general managers etc) and small to medium sized business owners. Predominately male aged 35+
Industry/Entity Type
Marketing
Requirements
Must have
- BRAND PERSONALITY
The successful design will communicate brand personality. I am a professional, results-driven entrepreneur, but want to show off my creative flair.
MEMORABILITY
Looking for a unique and eye-catching design. Am considering special printing effects (die cuts, letterpress, interactive elements, embossing, foiling etc) or a striking minimalist approach.
Nice to have
- I have a mission that could be incorporated on reverse if room -
Turning insights into actions & passion into profit.
Should not have
- Use of pink or green.

```html
<!DOCTYPE html>
<html lang="en">
<head>
<meta charset="utf-8">
<title>Tolvarin Stationery</title>
<link href="https://fonts.googleapis.com/css2?family=Barlow:wght@400;500;600;700&display=swap" rel="stylesheet">
<style>
:root{
  --bg:#e6e6e6;
  --paper:#ffffff;
  --ink:#3d3d3d;
  --body:#2f2f2f;
  --muted:#6a6a6a;
  --band:#4a4a4a;
  --band-text:#d8d8d8;
  --card-dark:#4b4b4b;
  --card-dark-edge:#333333;
  --accent:#3f6fc4;
  --rule:#bdbdbd;
  --window:#ebebeb;
}
*{margin:0;padding:0;box-sizing:border-box}
html,body{width:1200px;height:1200px;overflow:hidden}
body{background:var(--bg);font-family:"Barlow",Arial,sans-serif;color:var(--body);position:relative}
.sheet{position:absolute;background:var(--paper)}

/* brand lockup */
.brand{position:absolute;display:flex;flex-direction:column;align-items:flex-start}
.brand-row{display:flex;align-items:center}
.brand-dot{border-radius:50%;background:var(--ink)}
.brand-name{font-weight:700;color:var(--ink);letter-spacing:.02em;line-height:1}
.brand-tagline{color:var(--ink);font-weight:500;letter-spacing:.03em;white-space:nowrap}

/* letterhead */
.letterhead{left:113px;top:151px;width:616px;height:869px}
.letterhead .brand{left:62px;top:148px}
.letterhead .brand-dot{width:22px;height:22px;margin-right:10px}
.letterhead .brand-name{font-size:34px}
.letterhead .brand-tagline{font-size:8.5px;margin-top:6px}
.letter{position:absolute;left:61px;top:243px;width:451px;font-size:14.6px;line-height:18.2px;letter-spacing:.25px}
.letter-salutation{font-weight:500;margin-bottom:16px;color:#111;letter-spacing:0}
.letter p{text-align:justify;margin-bottom:18px}
.letter-closing{position:absolute;left:59px;top:637px;font-size:16px;line-height:21px;color:#333}
.signature{position:absolute;left:52px;top:712px;width:140px;height:46px;background:linear-gradient(90deg,#cfe0ef,#e9f1f8)}
.letter-footer{position:absolute;left:0;bottom:0;width:100%;height:50px;background:var(--band);color:var(--band-text);font-size:10.5px;display:flex;align-items:center;justify-content:center}
.letter-footer b{color:#fff;font-weight:600;margin-right:3px}
.letter-footer span{margin-right:6px}

/* envelopes */
.envelope-front{left:767px;top:100px;width:384px;height:197px}
.envelope-front .brand{left:34px;top:56px}
.envelope-front .brand-dot{width:8px;height:8px;margin-right:4px}
.envelope-front .brand-name{font-size:15px}
.envelope-front .brand-tagline{font-size:3.6px;margin-top:3px}
.env-rule{position:absolute;left:4px;top:118px;width:239px;height:1px;background:var(--ink)}
.env-window{position:absolute;left:256px;top:94px;width:101px;height:50px;background:var(--window);border-radius:5px}
.env-details{position:absolute;left:33px;top:135px;font-size:5.6px;line-height:7.5px;color:var(--muted)}
.env-details b{color:var(--ink);font-weight:600}
.envelope-back{left:765px;top:335px;width:383px;height:197px}
.envelope-back svg{position:absolute;left:0;top:0}
.envelope-back .brand{left:171px;top:47px}
.envelope-back .brand-dot{width:5px;height:5px;margin-right:3px}
.envelope-back .brand-name{font-size:9px}
.envelope-back .brand-tagline{font-size:2.4px;margin-top:2px}

/* business cards */
.card-front{left:810px;top:598px;width:279px;height:160px;background:radial-gradient(ellipse at 50% 35%,#5e5e5e 0%,var(--card-dark) 45%,var(--card-dark-edge) 100%)}
.card-front .brand{left:86px;top:92px}
.card-front .brand-dot{width:10px;height:10px;margin-right:5px;background:#fff}
.card-front .brand-name{font-size:21px;color:#fff}
.card-front .brand-tagline{font-size:5px;margin-top:4px;color:#fff}
.card-back{left:811px;top:812px;width:276px;height:160px}
.card-back .brand{left:17px;top:95px}
.card-back .brand-dot{width:9px;height:9px;margin-right:4px}
.card-back .brand-name{font-size:19px}
.card-back .brand-tagline{font-size:4.4px;margin-top:3px}
.card-divider{position:absolute;left:134px;top:60px;width:1px;height:62px;background:var(--rule)}
.card-contact{position:absolute;left:146px;top:55px;color:var(--muted);font-size:5.3px;line-height:7.3px}
.card-contact .person{font-size:9.5px;line-height:11px;color:var(--accent);font-weight:500}
.card-contact .role{font-size:7px;line-height:9px;margin-bottom:11px}
.card-contact .creds{margin-bottom:4px}
.card-contact b{color:var(--ink);font-weight:600}
.card-tab{position:absolute;right:0;top:89px;width:10px;height:31px;background:var(--accent)}
</style>
</head>
<body>

<section class="sheet letterhead">
  <div class="brand">
    <div class="brand-row"><span class="brand-dot"></span><span class="brand-name">TOLVARIN</span></div>
    <span class="brand-tagline">CLEAR STRATEGY. BOLD OUTCOMES.</span>
  </div>
  <div class="letter">
    <div class="letter-salutation">Dear Someone Somebody</div>
    <p>Lorem ipsum dolor sit amet, consectetur adipiscing elit. Donec orci purus, luctus vitae dignissim eu, iaculis sed purus. Vivamus faucibus, ipsum nec aliquet viverra, leo mauris condimentum ligula, sit s et auctor mi. Fusce vel massa nulla. Phasellus nec eros mauris,</p>
    <p>Quisque scelerisque sagittis nulla at porttitor. Mauris a justo et tellus interdum tristique. Sed id augue vitae urna euismod commodo aliquet a quam. Pellentesque arcu velit, cursus et malesuada ut, consequat et diam. Nullce aliquet faucibus ultricies. Morbi semper, est id tincidunt gravida, sem arcu adipiscing lacus, ac bibendum nulla leo eu purus. Quisque nec d</p>
    <p>Vivamus vehicula accumsan lacinia. Aliquam erat volutpat. Pellentesque consequat venenatis velit non gravida. Etiam et sem et nulla congue aliquam sed eget augue. Nulla facilisi. Pellentesque habitant morbi tristique senectus et netus et malesuada fames ac turpis egestas. Nulla a elit at sem iaculis congue. Nullam mollis tristique lobortis.</p>
  </div>
  <div class="letter-closing">Your Sincerely,<br>Somebody,</div>
  <div class="signature" role="img" aria-label="Handwritten signature in blue ink"></div>
  <footer class="letter-footer">
    <b>Mobile:</b><span>04XX-XXX-XXX</span>
    <b>email:</b><span>info@tolvarin.com.au</span>
    <b>website:</b><span>www.tolvarin.com.au</span>
  </footer>
</section>

<section class="sheet envelope-front">
  <div class="brand">
    <div class="brand-row"><span class="brand-dot"></span><span class="brand-name">TOLVARIN</span></div>
    <span class="brand-tagline">CLEAR STRATEGY. BOLD OUTCOMES.</span>
  </div>
  <div class="env-rule"></div>
  <div class="env-window"></div>
  <div class="env-details">
    B Com. Strategy, Grad Cert Brand Mgmt, MIM<br>
    <b>Mobile:</b> 04XX-XXX-XXX<br>
    <b>email:</b> info@tolvarin.com.au<br>
    <b>website:</b> www.tolvarin.com.au
  </div>
</section>

<section class="sheet envelope-back">
  <svg width="383" height="197" viewBox="0 0 383 197">
    <polyline points="0,4 191,80 383,4" fill="none" stroke="#d6d6d6" stroke-width="1"/>
    <line x1="6" y1="192" x2="150" y2="75" stroke="#dadada" stroke-width="1"/>
    <line x1="377" y1="192" x2="240" y2="75" stroke="#dadada" stroke-width="1"/>
  </svg>
  <div class="brand">
    <div class="brand-row"><span class="brand-dot"></span><span class="brand-name">TOLVARIN</span></div>
    <span class="brand-tagline">CLEAR STRATEGY. BOLD OUTCOMES.</span>
  </div>
</section>

<section class="sheet card-front">
  <div class="brand">
    <div class="brand-row"><span class="brand-dot"></span><span class="brand-name">TOLVARIN</span></div>
    <span class="brand-tagline">CLEAR STRATEGY. BOLD OUTCOMES.</span>
  </div>
</section>

<section class="sheet card-back">
  <div class="brand">
    <div class="brand-row"><span class="brand-dot"></span><span class="brand-name">TOLVARIN</span></div>
    <span class="brand-tagline">CLEAR STRATEGY. BOLD OUTCOMES.</span>
  </div>
  <div class="card-divider"></div>
  <div class="card-contact">
    <div class="person">Your Name</div>
    <div class="role">Principal</div>
    <div class="creds">B Com. Strategy, Grad Cert Brand Mgmt, MIM</div>
    <b>Mobile:</b> 04XX-XXX-XXX<br>
    <b>Email:</b> info@tolvarin.com.au<br>
    <b>website:</b> www.tolvarin.com.au
  </div>
  <div class="card-tab"></div>
</section>

</body>
</html>
```